Super elegant, crisp & clean Business card design required

We recently upgraded our branding - which is on our website - talvendoraphoto.com

I would like a simple, yet elegant, clean business card design please.

The font of my logo is Cinzel - and because of the natural colour - it's best to have this on a black background.

I would like to have the back of the business card - with simply my logo.

PLEASE DO NOT SUBMIT A COMPLICATED / UNCLEAN DESIGN

Industry/Entity Type

Business

Contact Information for Business Card

Talven Doroshko Photography

Font styles to use
Other font styles liked:
• Cinzel

Requirements
Must have
• A backpage with nothing but my logo
• Simple design - stands out
Should not have
• Colour that dont align with my logo
• Over complicated '/ non symmetrical design

```html
<!DOCTYPE html>
<html lang="en">
<head>
<meta charset="utf-8">
<title>Talven Doroshko Photography — Business Card</title>
<link rel="stylesheet" href="https://fonts.googleapis.com/css2?family=Cinzel:wght@400&family=Questrial&display=swap">
<style>
  :root {
    --backdrop: #1b1b1b;
    --card: #030303;
    --card-edge: #2a2a2a;
    --gold: #a8957a;
    --gold-soft: #8f7e66;
  }
  * { margin: 0; padding: 0; box-sizing: border-box; }
  html, body { width: 1200px; height: 741px; overflow: hidden; }
  body { background: var(--backdrop); position: relative; font-family: "Questrial", sans-serif; }

  .card {
    position: absolute;
    top: 229px;
    width: 494px;
    height: 282px;
    background: var(--card);
    border: 1px solid var(--card-edge);
    border-radius: 14px;
  }
  .card--front { left: 99px; }
  .card--back { left: 608px; }

  .brand { position: absolute; text-align: center; color: var(--gold); font-family: "Cinzel", serif; font-weight: 400; }
  .brand__mark { display: block; margin: 0 auto; }
  .brand__name { display: block; white-space: nowrap; }
  .brand__tag { display: block; white-space: nowrap; }

  .card--front .brand { left: 4px; width: 240px; top: 92px; }
  .card--front .brand__mark { width: 56px; height: 56px; margin-bottom: 10px; }
  .card--front .brand__name { font-size: 18px; line-height: 20px; }
  .card--front .brand__tag { font-size: 8px; letter-spacing: 6.2px; margin-top: 1px; padding-left: 6px; }

  .divider { position: absolute; left: 242px; top: 72px; width: 1px; height: 140px; background: var(--gold-soft); }

  .person { position: absolute; left: 262px; top: 62px; color: var(--gold); }
  .person__name { font-family: "Cinzel", serif; font-size: 20px; line-height: 22px; letter-spacing: 0.3px; }
  .person__role { font-size: 13px; line-height: 14px; }

  .contact { position: absolute; left: 262px; top: 160px; list-style: none; color: var(--gold); font-size: 13px; }
  .contact li { display: flex; align-items: center; height: 17px; white-space: nowrap; }
  .contact svg { width: 11px; height: 11px; margin-right: 7px; flex: none; }

  .card--back .brand { left: 0; width: 100%; top: 80px; }
  .card--back .brand__mark { width: 64px; height: 64px; margin-bottom: 12px; }
  .card--back .brand__name { font-size: 21px; line-height: 23px; }
  .card--back .brand__tag { font-size: 9.5px; letter-spacing: 8px; margin-top: 2px; padding-left: 8px; }
</style>
</head>
<body>
  <section class="card card--front" aria-label="Business card front">
    <div class="brand">
      <svg class="brand__mark" viewBox="0 0 56 56" aria-hidden="true"><circle cx="28" cy="28" r="26" fill="none" stroke="#a8957a" stroke-width="1.2"/></svg>
      <span class="brand__name">Talven Doroshko</span>
      <span class="brand__tag">PHOTOGRAPHY</span>
    </div>
    <div class="divider"></div>
    <div class="person">
      <p class="person__name">ALDOUS MERRIN</p>
      <p class="person__role">Chief Executive Officer</p>
    </div>
    <ul class="contact">
      <li><svg viewBox="0 0 12 12" aria-hidden="true"><path d="M3 1 L5 3.5 L4 5 Q5 7.5 7 8 L8.5 7 L11 9 L9.5 11 Q4 10.5 1 3 Z" fill="#a8957a"/></svg>44 7700 900415</li>
      <li><svg viewBox="0 0 12 12" aria-hidden="true"><rect x="0.5" y="2.5" width="11" height="7" fill="#a8957a"/><path d="M0.5 2.5 L6 7 L11.5 2.5" fill="none" stroke="#030303" stroke-width="1"/></svg>studio@talvendoraphoto.com</li>
      <li><svg viewBox="0 0 12 12" aria-hidden="true"><g fill="none" stroke="#a8957a" stroke-width="1"><circle cx="6" cy="6" r="5"/><ellipse cx="6" cy="6" rx="2.2" ry="5"/><path d="M1 6 H11 M2 3.5 H10 M2 8.5 H10"/></g></svg>www.talvendoraphoto.com</li>
    </ul>
  </section>

  <section class="card card--back" aria-label="Business card back">
    <div class="brand">
      <svg class="brand__mark" viewBox="0 0 64 64" aria-hidden="true"><circle cx="32" cy="32" r="30" fill="none" stroke="#a8957a" stroke-width="1.2"/></svg>
      <span class="brand__name">Talven Doroshko</span>
      <span class="brand__tag">PHOTOGRAPHY</span>
    </div>
  </section>
</body>
</html>
```